COVID-19 Accredited CME Impact Infographic

We want an infographic showing how much COVID-19 Continuing Medical Education we have accredited and its impact. Our website is at https://med.kelbrook.edu/cme/COVID19/education.html The attached document is intended to simply show the elements. You have complete freedom on design. We will be updating the numbers weekly so it is important that we have the files so that we can update it. This can be done in powerpoint, publisher, word, in-design, illustrator. Don't use crazy fonts that we wont have.

Target Market(s)

Internal to Kelbrook. We just want to show the impact of our work

Industry/Entity Type

Education

Requirements
Must have
• We must be able to update the numbers ourselves.

See attached document for the pieces that we want.

The sizes of the numbers in the attached are based on importance to us.
Nice to have
• Not mandatory but try to use these colors. https://med.kelbrook.edu/identity/color-palette.html

I was thinking that perhaps the big number could be done in traditional train. Like this: https://www.pixelvarda.com/image-illustration/flip-board-under-constuction-page-isolated-4816203957

```html
<!DOCTYPE html>
<html lang="en">
<head>
<meta charset="utf-8">
<title>COVID-19 CME Impact – Kelbrook Medicine</title>
<link href="https://fonts.googleapis.com/css2?family=Roboto:wght@300;400;500;700;900&family=Share+Tech+Mono&display=swap" rel="stylesheet">
<style>
  :root {
    --bg-deep: #08081c;
    --bg-navy: #16163d;
    --ring-navy: #2a2a5e;
    --logo-white: #ffffff;
    --brand-red: #8c1515;
    --ink-dark: #0f1b33;
    --text-light: #f2f2f6;
    --text-muted: #c9c9d6;
    --line: #cfd3e0;
    --views-blue: #22a8ee;
    --views-blue-dark: #1378b8;
    --activities-cyan: #3cc3d6;
    --states-lime: #a6cc36;
    --countries-gold: #d7a032;
    --live-magenta: #b946d2;
    --cme-green: #3dbd72;
    --virus-red: #8e1f3a;
  }
  * { box-sizing: border-box; margin: 0; padding: 0; }
  html, body { width: 1200px; height: 693px; overflow: hidden; background: var(--bg-deep); }
  .infographic {
    position: relative; width: 1200px; height: 693px; overflow: hidden;
    background: radial-gradient(ellipse at 60% 40%, var(--bg-navy) 0%, var(--bg-deep) 75%);
    font-family: "Roboto", Arial, sans-serif; color: var(--text-light);
  }
  .world-map {
    position: absolute; left: 120px; top: 120px; width: 1060px; height: 500px;
    border-radius: 45% 40% 35% 50%;
    background: radial-gradient(ellipse at 50% 40%, rgba(60,60,100,0.35), rgba(60,60,100,0) 70%);
  }
  .globe-halo {
    position: absolute; left: 672px; top: 124px; width: 616px; height: 616px;
    border-radius: 50%; background: rgba(255,255,255,0.035);
  }
  .date-arc {
    position: absolute; left: 857px; top: -70px; width: 175px; height: 100px;
    border-radius: 50%; border: 6px solid #3a3a62; background: #55556f;
  }
  .brand-badge {
    position: absolute; left: -40px; top: -40px; width: 300px; height: 184px;
    border-radius: 0 0 60% 50% / 0 0 70% 70%;
    background: var(--logo-white); box-shadow: 6px 6px 0 4px var(--ring-navy);
    display: flex; align-items: center; padding-left: 60px; padding-top: 44px; gap: 10px;
  }
  .brand-mark { width: 30px; height: 30px; background: var(--brand-red); }
  .brand-name { font-family: "Roboto", Arial, sans-serif; font-weight: 500; font-size: 28px; color: var(--brand-red); line-height: 1; }
  .date-block { position: absolute; right: 46px; top: 24px; text-align: right; }
  .date-label { font-weight: 300; font-size: 26px; color: var(--text-muted); margin-right: 70px; }
  .date-value { font-family: "Share Tech Mono", monospace; font-size: 60px; letter-spacing: 2px; color: var(--text-light); line-height: 1; }
  .connectors { position: absolute; left: 0; top: 0; }
  .views-dome {
    position: absolute; left: 288px; top: 194px; width: 192px; height: 192px; border-radius: 50%;
    background: var(--views-blue); border: 6px solid var(--views-blue-dark);
    text-align: center; padding-top: 48px;
    font-weight: 700; font-size: 26px; line-height: 28px; color: var(--ink-dark);
  }
  .views-bar {
    position: absolute; left: 179px; top: 304px; width: 407px; height: 64px; border-radius: 28px;
    background: linear-gradient(180deg, #3ec0fa, var(--views-blue)); box-shadow: 0 5px 0 var(--views-blue-dark);
    text-align: center; font-weight: 700; font-size: 46px; line-height: 64px; color: var(--ink-dark);
  }
  .stat { position: absolute; width: 164px; height: 90px; text-align: center; }
  .stat-tab {
    position: absolute; left: 38px; top: 14px; width: 88px; height: 88px; border-radius: 50%;
    background: var(--c); box-shadow: inset 0 -5px 0 rgba(0,0,0,0.18);
    font-weight: 500; font-size: 20px; color: var(--ink-dark); padding-top: 44px;
  }
  .stat-label {
    position: relative; height: 44px; border-radius: 22px; background: var(--c);
    box-shadow: 0 4px 0 rgba(0,0,0,0.2);
    font-size: 15px; line-height: 44px; color: var(--text-light); font-weight: 400;
  }
  .stat--activities { --c: var(--activities-cyan); left: 92px; top: 407px; }
  .stat--states { --c: var(--states-lime); left: 300px; top: 405px; }
  .stat--countries { --c: var(--countries-gold); left: 510px; top: 400px; }
  .stat--live { --c: var(--live-magenta); left: 198px; top: 510px; }
  .stat--cme { --c: var(--cme-green); left: 406px; top: 507px; }
  .title-rule { position: absolute; left: 752px; top: 313px; width: 438px; height: 2px; background: #4a4a70; }
  .virus-art {
    position: absolute; left: 772px; top: 384px; width: 96px; height: 96px; border-radius: 50%;
    background: radial-gradient(circle at 40% 40%, #b83455, var(--virus-red) 60%, rgba(142,31,58,0) 72%);
  }
  .title { position: absolute; left: 746px; top: 312px; line-height: 1; }
  .title-main { font-weight: 900; font-size: 82px; letter-spacing: 1px; color: #e6e6ec; }
  .title-sub { font-weight: 400; font-size: 84px; color: #e6e6ec; margin-left: 116px; margin-top: -6px; }
</style>
</head>
<body>
<main class="infographic">
  <div class="world-map" role="img" aria-label="Faint world map in the background"></div>
  <div class="globe-halo"></div>
  <div class="date-arc"></div>

  <header class="brand-badge">
    <span class="brand-mark"></span>
    <span class="brand-name">Kelbrook Medicine</span>
  </header>

  <div class="date-block">
    <div class="date-label">Date:</div>
    <div class="date-value">04/10/20</div>
  </div>

  <svg class="connectors" width="1200" height="693" aria-hidden="true">
    <g stroke="var(--line)" stroke-width="1.5" stroke-dasharray="3 3">
      <line x1="210" y1="368" x2="210" y2="407"/>
      <line x1="382" y1="368" x2="382" y2="405"/>
      <line x1="546" y1="368" x2="546" y2="400"/>
    </g>
    <g stroke="var(--line)" stroke-width="1.2">
      <line x1="279" y1="368" x2="279" y2="510"/>
      <line x1="488" y1="368" x2="488" y2="507"/>
    </g>
  </svg>

  <div class="views-dome">#of total on-<br>demand views</div>
  <div class="views-bar">1,209,987</div>

  <div class="stat stat--activities"><div class="stat-tab">23</div><div class="stat-label">#of Activities</div></div>
  <div class="stat stat--states"><div class="stat-tab">26</div><div class="stat-label">#of states</div></div>
  <div class="stat stat--countries"><div class="stat-tab">12</div><div class="stat-label">#of Countries</div></div>
  <div class="stat stat--live"><div class="stat-tab">23,098</div><div class="stat-label">#of live Learners</div></div>
  <div class="stat stat--cme"><div class="stat-tab">5,879</div><div class="stat-label">#of CME Learners</div></div>

  <div class="title-rule"></div>
  <div class="virus-art" role="img" aria-label="Red coronavirus particle illustration"></div>
  <h1 class="title">
    <div class="title-main">COVID-19</div>
    <div class="title-sub">CME</div>
  </h1>
</main>
</body>
</html>
```